Brightloom MAX Fiber Internet Service

Ad is for advertising fiber optic internet service in West Point, NE. Ad should convey fast internet. Pricing is: http://brightloomlink.example/index.php/template-info/fiber-to-the-home

Promotion, free installation if ordered before September 31st. Telephone service also available.

To be used for chatterbook advertising.

Target Market(s)

New customers, PolarNet, Dunmoor customers.

Industry/Entity Type

Telecommunications

Requirements
Must have
• Brightloom logo, conform to chatterbook guidelines including 20% text rule
Nice to have
• Convey modern, fast, high tech, link to pricing, office phone number. Be able to change date for free installation if ordered by. Complement Brightloom colors.
Should not have
• Do not use full name "Brightloom Wireless, Inc." Only use "Brightloom"

```html
<!DOCTYPE html>
<html lang="en">
<head>
<meta charset="utf-8">
<title>Brightloom MAX Fiber – Fiber to the Home</title>
<link href="https://fonts.googleapis.com/css2?family=Oswald:wght@500;600;700&family=Montserrat:wght@500;700&display=swap" rel="stylesheet">
<style>
  :root {
    --navy-deep: #061a4a;
    --navy: #0b2a73;
    --navy-glow: #1740a3;
    --teal-dark: #2577a3;
    --teal: #3a9fc2;
    --band: #3b3b3d;
    --band-fold: #1e1e20;
    --white: #ffffff;
    --silver: #c9cbd0;
    --ink-blue: #0f5c96;
    --line-teal: #2ea6c9;
    --logo-teal: #2d8fb8;
  }
  * { box-sizing: border-box; margin: 0; padding: 0; }
  html, body { width: 1200px; height: 1200px; overflow: hidden; background: #ffffff; }
  .ad {
    position: relative; width: 1200px; height: 1200px; overflow: hidden;
    background: var(--navy-deep);
    font-family: 'Oswald', sans-serif; color: var(--white);
  }
  .ad__backdrop {
    position: absolute; inset: 0;
    background:
      radial-gradient(ellipse 60% 40% at 65% 10%, rgba(30,70,180,.7), transparent 70%),
      radial-gradient(ellipse 70% 30% at 30% 45%, rgba(25,65,170,.55), transparent 70%),
      radial-gradient(ellipse 50% 40% at 90% 60%, rgba(20,60,160,.5), transparent 70%),
      linear-gradient(160deg, var(--navy) 0%, var(--navy-deep) 55%, #0a2363 100%);
  }
  .brand {
    position: absolute; left: 103px; top: 112px;
    display: flex; align-items: center; gap: 16px;
  }
  .brand__dot {
    width: 58px; height: 58px; border-radius: 50%;
    border: 5px solid var(--logo-teal);
  }
  .brand__name {
    font-family: 'Oswald', sans-serif; font-weight: 700;
    font-size: 84px; line-height: 1; letter-spacing: 1px;
    color: var(--logo-teal);
  }
  .partner-badge {
    position: absolute; left: 922px; top: 82px; width: 177px; height: 140px;
    border: 4px solid var(--white); border-radius: 18px; background: var(--navy-deep);
  }
  .headline {
    position: absolute; left: 0; right: 0; top: 270px; text-align: center;
    white-space: nowrap;
    font-weight: 700; font-size: 134px; line-height: 1; letter-spacing: 0;
    background: linear-gradient(180deg, #ffffff 30%, #b9bcc3 100%);
    -webkit-background-clip: text; background-clip: text; color: transparent;
  }
  .plan {
    position: absolute; text-align: center; border-radius: 10px; white-space: nowrap;
    background: linear-gradient(90deg, var(--teal-dark), var(--teal));
  }
  .plan--fast   { left: 94px;  top: 500px; width: 308px; height: 343px; }
  .plan--faster { left: 798px; top: 500px; width: 308px; height: 343px; }
  .plan--max    { left: 402px; top: 454px; width: 396px; height: 423px; z-index: 2;
                  box-shadow: 0 0 18px rgba(0,0,0,.25); }
  .plan__tab {
    position: absolute; left: 73px; top: -10px; width: 255px; height: 45px;
    background: var(--white); color: var(--ink-blue);
    clip-path: polygon(0 0, 100% 0, 90% 100%, 10% 100%);
    font-weight: 600; font-size: 30px; line-height: 45px;
  }
  .plan__speed { font-weight: 500; font-size: 36px; line-height: 1; }
  .plan__data  { font-weight: 500; font-size: 40px; line-height: 1; margin-top: 12px; }
  .plan--fast .plan__speed, .plan--faster .plan__speed { margin-top: 36px; }
  .plan--max .plan__speed { font-size: 44px; margin-top: 62px; }
  .plan--max .plan__data  { font-size: 47px; margin-top: 10px; }
  .price-band {
    position: absolute; height: 80px; background: var(--band);
    font-family: 'Montserrat', sans-serif; font-weight: 700;
    font-size: 62px; line-height: 80px; text-align: center;
  }
  .price-band::before, .price-band::after {
    content: ""; position: absolute; top: -10px; width: 22px; height: 10px; background: var(--band-fold);
  }
  .price-band::before { left: 0; clip-path: polygon(100% 0, 100% 100%, 0 100%); }
  .price-band::after  { right: 0; clip-path: polygon(0 0, 100% 100%, 0 100%); }
  .plan--fast .price-band   { left: -22px; right: 0; top: 142px; }
  .plan--faster .price-band { left: 0; right: -22px; top: 142px; }
  .plan--max .price-band    { left: -26px; right: -26px; top: 182px; height: 96px; line-height: 96px; font-size: 74px;
                              background: linear-gradient(90deg, #2c2c2e, var(--band) 20%, var(--band) 80%, #2c2c2e); }
  .plan__extra {
    position: absolute; left: 0; right: 0; top: 290px;
    font-weight: 500; font-size: 22px; line-height: 1;
  }
  .plan__tag {
    position: absolute; background: var(--white); border-radius: 4px; color: var(--ink-blue);
    font-weight: 700; font-style: italic; font-size: 40px; line-height: 55px; letter-spacing: -1px;
  }
  .plan--fast .plan__tag, .plan--faster .plan__tag { left: 31px; width: 228px; top: 252px; height: 55px; }
  .plan--max .plan__tag { left: 51px; width: 294px; top: 336px; height: 55px; }
  .offer {
    position: absolute; left: 106px; top: 947px; width: 989px; height: 120px;
    border: 2px solid var(--line-teal); border-top: none; border-radius: 0 0 6px 6px;
    font-family: 'Montserrat', sans-serif; text-align: center; white-space: nowrap;
  }
  .offer__rule { position: absolute; top: 0; height: 2px; background: var(--line-teal); }
  .offer__rule--left  { left: -2px; width: 194px; }
  .offer__rule--right { right: -2px; width: 190px; }
  .offer__title {
    position: absolute; left: 0; right: 0; top: -28px;
    font-weight: 700; font-size: 50px; line-height: 54px; letter-spacing: 1px;
  }
  .offer__body {
    position: absolute; left: 0; right: 0; top: 31px;
    font-weight: 500; font-size: 31px; line-height: 40px;
  }
  .contact {
    position: absolute; left: 132px; top: 1112px; height: 46px;
    display: flex; align-items: center; white-space: nowrap;
    font-family: 'Montserrat', sans-serif; font-weight: 500; font-size: 36px;
  }
  .contact__item { display: flex; align-items: center; gap: 12px; }
  .contact__divider { width: 2px; height: 28px; background: var(--line-teal); margin: 0 22px 0 22px; }
  .contact__icon { width: 26px; height: 26px; flex: none; }
</style>
</head>
<body>
<main class="ad">
  <div class="ad__backdrop" role="img" aria-label="Glowing blue fiber optic cables sweeping across a dark navy background"></div>

  <div class="brand">
    <span class="brand__dot"></span>
    <span class="brand__name">BRIGHTLOOM</span>
  </div>
  <div class="partner-badge" aria-hidden="true"></div>

  <h1 class="headline">FIBER TO THE HOME</h1>

  <section class="plan plan--fast">
    <p class="plan__speed">100 Meg / 10 Meg</p>
    <p class="plan__data">UNLIMITED DATA</p>
    <p class="price-band">$50.00</p>
    <p class="plan__tag">FAST</p>
  </section>

  <section class="plan plan--max">
    <p class="plan__tab">THE MAX PLAN!</p>
    <p class="plan__speed">100 Meg / 10 Meg</p>
    <p class="plan__data">UNLIMITED DATA</p>
    <p class="price-band">$90.00</p>
    <p class="plan__extra">INCLUDES WHOLEHOME WIFI!</p>
    <p class="plan__tag">FASTEST</p>
  </section>

  <section class="plan plan--faster">
    <p class="plan__speed">200 Meg / 20 Meg</p>
    <p class="plan__data">UNLIMITED DATA</p>
    <p class="price-band">$70.00</p>
    <p class="plan__tag">FASTER</p>
  </section>

  <section class="offer">
    <span class="offer__rule offer__rule--left"></span>
    <span class="offer__rule offer__rule--right"></span>
    <h2 class="offer__title">LIMITED TIME OFFER</h2>
    <p class="offer__body">Free Installation If Ordered Before September 31st.<br>Telephone Service Also Available.</p>
  </section>

  <footer class="contact">
    <span class="contact__item">
      <svg class="contact__icon" viewBox="0 0 26 26" aria-hidden="true">
        <circle cx="13" cy="13" r="11.5" fill="none" stroke="#2ea6c9" stroke-width="2"/>
        <path d="M9 7.5l2 0 1 3-1.4 1.2a7 7 0 0 0 3.7 3.7L15.5 14l3 1v2a1.5 1.5 0 0 1-1.6 1.5A10 10 0 0 1 7.5 9.1 1.5 1.5 0 0 1 9 7.5z" fill="none" stroke="#2ea6c9" stroke-width="1.6" stroke-linejoin="round"/>
      </svg>
      555-014-2290
    </span>
    <span class="contact__divider"></span>
    <span class="contact__item">
      <svg class="contact__icon" viewBox="0 0 26 26" aria-hidden="true">
        <g fill="none" stroke="#2ea6c9" stroke-width="1.8">
          <circle cx="13" cy="13" r="11"/>
          <ellipse cx="13" cy="13" rx="5" ry="11"/>
          <path d="M2 13h22M4 7.5h18M4 18.5h18"/>
        </g>
      </svg>
      www.brightloomlink.example
    </span>
  </footer>
</main>
</body>
</html>
```